Business Card Design Project

New Business Card design for Vantroke Technology Ltd using new Logo and new Tagline for staffing company.

About us from our website - www.vantroke-example.com:

VanTroke is a leading and recognized Electronic Entertainment, Workforce Augmentation, and Project Management solutions provider with clients in Electronic Entertainment, Legal, Technology, Government and other verticals that range in size from start up organizations to Meridex 500 companies. VanTroke is certified as an 8(a) minority and woman owned enterprise, established in 1998.

Target Market(s)

Companies in Electronic Entertainment, Legal, Government and Technology

Industry/Entity Type

Business

Requirements
Must have
• Must include in small letters the following information on back:

Established in 1998
8(a)(w)(e), Cage #7KTR9, DUNS #415260387

Front should have the following:
Pavel Orrin
Vice President
5678 Bramwick Lane
Tollerby, TB 654321
555-301-4826 X 100
555-309-1175 Fax
555-301-4826 Toll Free
name@vantroke-example.com

Our Tagline: Connect • Collaborate • Achieve

```html
<!DOCTYPE html>
<html lang="en">
<head>
<meta charset="utf-8">
<title>VanTroke Business Cards</title>
<link rel="stylesheet" href="https://fonts.googleapis.com/css2?family=Arimo:wght@400;700&display=swap">
<style>
  :root {
    --page: #ffffff;
    --card: #000000;
    --brand-blue: #0b5cad;
    --text-blue: #1565c0;
    --white: #ffffff;
    --shadow: rgba(0, 0, 0, 0.35);
  }
  * { box-sizing: border-box; margin: 0; padding: 0; }
  html, body {
    width: 1200px;
    height: 900px;
    overflow: hidden;
    background: var(--page);
    font-family: "Arimo", Arial, sans-serif;
  }
  .canvas { position: relative; width: 1200px; height: 900px; }
  .card {
    position: absolute;
    width: 640px;
    height: 385px;
    background: var(--card);
    border-radius: 18px;
    overflow: hidden;
    box-shadow: 2px 4px 8px var(--shadow);
  }
  .card--front { left: 85px; top: 45px; }
  .card--back { left: 478px; top: 465px; }

  .brand {
    display: flex;
    align-items: center;
    gap: 10px;
    font-weight: 700;
    color: var(--white);
    letter-spacing: -1px;
  }
  .brand__dot {
    width: 16px;
    height: 16px;
    border-radius: 50%;
    background: var(--brand-blue);
  }
  .card--front .brand {
    position: absolute;
    left: 50px;
    top: 140px;
    font-size: 46px;
  }
  .divider {
    position: absolute;
    left: 302px;
    top: 20px;
    width: 3px;
    height: 265px;
    background: linear-gradient(to bottom, rgba(11,92,173,0) 0%, var(--brand-blue) 55%, rgba(11,92,173,0) 100%);
  }
  .contact {
    position: absolute;
    left: 345px;
    top: 42px;
  }
  .contact__name {
    font-size: 27px;
    font-weight: 700;
    color: var(--text-blue);
    line-height: 1;
  }
  .contact__title {
    font-size: 21px;
    font-weight: 700;
    color: var(--white);
    margin-top: 3px;
    margin-bottom: 18px;
  }
  .contact__lines {
    list-style: none;
    font-size: 17px;
    line-height: 22px;
    color: var(--text-blue);
  }
  .tagline {
    position: absolute;
    left: 0;
    bottom: 0;
    width: 100%;
    height: 68px;
    background: var(--brand-blue);
    display: flex;
    justify-content: space-around;
    align-items: center;
    font-size: 22px;
    font-weight: 700;
    color: var(--white);
  }

  .card--back .brand {
    position: absolute;
    left: 0;
    right: 0;
    top: 120px;
    justify-content: center;
    font-size: 66px;
  }
  .credentials {
    position: absolute;
    left: 0;
    right: 0;
    top: 268px;
    text-align: center;
    color: var(--text-blue);
  }
  .credentials__est {
    font-size: 18px;
    font-weight: 700;
    margin-bottom: 18px;
  }
  .credentials__ids {
    list-style: none;
    font-size: 11px;
    line-height: 14px;
  }
</style>
</head>
<body>
<main class="canvas">
  <section class="card card--front" aria-label="Business card front">
    <div class="brand"><span class="brand__dot"></span>VanTroke</div>
    <div class="divider"></div>
    <div class="contact">
      <p class="contact__name">Pavel Orrin</p>
      <p class="contact__title">Vice President</p>
      <ul class="contact__lines">
        <li>5678 Bramwick Lane</li>
        <li>Tollerby, TB 654321</li>
        <li>555-301-4826 X 100</li>
        <li>555-309-1175 Fax</li>
        <li>555-301-4826 Toll Free</li>
        <li>name@vantroke-example.com</li>
      </ul>
    </div>
    <div class="tagline">
      <span>Connect</span>
      <span>Collaborate</span>
      <span>Achieve</span>
    </div>
  </section>

  <section class="card card--back" aria-label="Business card back">
    <div class="brand"><span class="brand__dot"></span>VanTroke</div>
    <div class="credentials">
      <p class="credentials__est">Established in 1998</p>
      <ul class="credentials__ids">
        <li>8(a)(w)(e)</li>
        <li>Cage #7KTR9</li>
        <li>DUNS #415260387</li>
      </ul>
    </div>
  </section>
</main>
</body>
</html>
```